Business Card Re-Design/Update

We'd like to update out business cards. I've included our current "Style guide" which has the colour scheme of the organisation in it. I've also included the branding files with logos etc in them.

I've also included a copy of one of our existing cards so that you can see how ugly/dated they look. I'd like a fresh modern corporate look.

Target Market(s)

These are for our clients, potential clients, industry contacts - like all business cards

Contact Information for Business Card

Name
Position
Company Address - Level 1, 47 Fernby Street, Carlow Qld 4072
Direct Phone
mobile
Email
Website -www.korvalit.com.au
Logo

Colors

Designer to choose colors to be used in the design.

Requirements
Must have
• Main Logo
• Cards will need to be editable to be able to personalize them for each new employee.
Nice to have
• The MapOut, ShipWell, KeepSteady would be okay to have if they can be sensibly and professionally added to the look without detracting from the main imagery.
• Maybe they could go on the back of the card? will leave this to your creative discretion as to whether/where they fit.
Should not have
• Should not have decorative or script fonts

```html
<!DOCTYPE html>
<html lang="en">
<head>
<meta charset="utf-8">
<title>korvalIT business card</title>
<link rel="stylesheet" href="https://fonts.googleapis.com/css2?family=Roboto:wght@400;500;700&family=Roboto+Condensed:wght@400;700&display=swap">
<style>
  :root {
    --red: #d0161e;
    --red-deep: #a90f15;
    --shadow-band: #2b2b2b;
    --ink: #262626;
    --paper: #f5f5f4;
    --backdrop: #e4e2df;
    --white: #ffffff;
  }
  * { margin: 0; padding: 0; box-sizing: border-box; }
  html, body { width: 1200px; height: 911px; overflow: hidden; }
  body {
    background: var(--backdrop);
    font-family: "Roboto", Arial, sans-serif;
    position: relative;
  }
  .card {
    position: absolute;
    width: 560px;
    height: 320px;
    overflow: hidden;
    box-shadow: 0 10px 28px rgba(0,0,0,.22);
  }
  .card-front { left: 70px; top: 110px; background: var(--paper); }
  .card-back {
    left: 570px; top: 480px;
    background: linear-gradient(135deg, var(--red-deep) 0%, var(--red) 70%);
  }
  .front-shapes { position: absolute; inset: 0; }

  .brand { position: absolute; display: flex; align-items: center; gap: 10px; }
  .brand-square { width: 22px; height: 22px; background: var(--red); }
  .brand-name { font-size: 30px; font-weight: 500; color: var(--ink); letter-spacing: -.5px; line-height: 1.2; }
  .card-front .brand { left: 30px; top: 116px; }

  .person { position: absolute; right: 28px; top: 40px; text-align: right; }
  .person-name {
    font-family: "Roboto Condensed", Arial, sans-serif;
    font-weight: 700; font-size: 20px; color: var(--red); text-transform: uppercase;
  }
  .person-role {
    font-family: "Roboto Condensed", Arial, sans-serif;
    font-size: 12.5px; color: var(--ink); margin-top: 2px;
  }

  .contact {
    position: absolute; left: 252px; top: 134px; width: 282px;
    font-family: "Roboto Condensed", Arial, sans-serif;
    font-size: 12.5px; color: var(--white); line-height: 1.55;
  }
  .contact-cols { display: flex; justify-content: space-between; }
  .contact-row { display: flex; align-items: center; gap: 6px; }
  .contact-row svg { width: 10px; height: 10px; flex: none; }
  .contact-email { margin-top: 4px; text-align: right; }
  .contact-rule { height: 1px; background: rgba(255,255,255,.6); width: 60px; margin: 4px 0 4px auto; }
  .contact-address { text-align: right; }

  .website {
    position: absolute; right: 30px; bottom: 30px;
    font-size: 12px; letter-spacing: 3px; color: var(--red);
  }

  .card-back .brand { left: 50%; top: 50%; transform: translate(-50%, -50%); gap: 14px; }
  .card-back .brand-square { width: 40px; height: 40px; background: var(--white); }
  .card-back .brand-name { color: var(--white); font-size: 44px; }

  .taglines {
    position: absolute; left: 34px; bottom: 28px;
    display: flex; align-items: center; gap: 14px;
    color: var(--white); font-size: 22px; font-weight: 500;
  }
  .tagline-divider { width: 1px; height: 20px; background: rgba(255,255,255,.7); }
</style>
</head>
<body>

<section class="card card-front" aria-label="Card front">
  <svg class="front-shapes" viewBox="0 0 560 320" width="560" height="320" aria-hidden="true">
    <polygon points="0,265 260,120 560,120 560,240 310,240 210,320 0,320" fill="var(--red)"/>
    <polygon points="310,240 342,240 242,320 210,320" fill="var(--shadow-band)"/>
    <polygon points="342,240 560,240 560,320 242,320" fill="var(--paper)"/>
  </svg>

  <div class="brand">
    <span class="brand-square"></span>
    <span class="brand-name">korvalIT</span>
  </div>

  <div class="person">
    <div class="person-name">Mara Kellett</div>
    <div class="person-role">Business Development Manager</div>
  </div>

  <div class="contact">
    <div class="contact-cols">
      <div>
        <div class="contact-row">
          <svg viewBox="0 0 10 10"><path d="M2 1 L4 1 L4.6 3 L3.4 3.8 Q4.4 5.8 6.2 6.6 L7 5.4 L9 6 L9 8 Q5 9 2.4 6 Q1 4 2 1Z" fill="#fff"/></svg>
          <span>+61 (0)7 3000 4821</span>
        </div>
        <div class="contact-row">
          <svg viewBox="0 0 10 10"><path d="M2 1 L4 1 L4.6 3 L3.4 3.8 Q4.4 5.8 6.2 6.6 L7 5.4 L9 6 L9 8 Q5 9 2.4 6 Q1 4 2 1Z" fill="#fff"/></svg>
          <span>+61 (0)7 3000 4822</span>
        </div>
      </div>
      <div>
        <div class="contact-row">
          <svg viewBox="0 0 10 10"><rect x="2.5" y="0.5" width="5" height="9" rx="1" fill="none" stroke="#fff"/></svg>
          <span>+61 (0)400 118 245</span>
        </div>
        <div class="contact-row">
          <svg viewBox="0 0 10 10"><rect x="1" y="3" width="8" height="6" fill="#fff"/><rect x="3" y="0.5" width="4" height="3" fill="none" stroke="#fff"/></svg>
          <span>+61 (0)7 3000 4830</span>
        </div>
      </div>
    </div>
    <div class="contact-email">mkellett@korvalit.com.au</div>
    <div class="contact-rule"></div>
    <div class="contact-address">Level 1, 47 Fernby Street, Carlow Qld 4072</div>
  </div>

  <div class="website">www.korvalit.com.au</div>
</section>

<section class="card card-back" aria-label="Card back">
  <div class="brand">
    <span class="brand-square"></span>
    <span class="brand-name">korvalIT</span>
  </div>
  <div class="taglines">
    <span>MapOut</span>
    <span class="tagline-divider"></span>
    <span>ShipWell</span>
    <span class="tagline-divider"></span>
    <span>KeepSteady</span>
  </div>
</section>

</body>
</html>
```